Realty Group Needs Classy, Contemporary Letterhead Design

We need a letterhead design for a new realty company located in NY, USA. We buy investment properties to rehabilitate and or keep in our rental portfolio.

```html
<!DOCTYPE html>
<html lang="en">
<head>
<meta charset="utf-8">
<title>Halvard Realty Group – Letterhead</title>
<link href="https://fonts.googleapis.com/css2?family=Open+Sans:wght@400;600;700&display=swap" rel="stylesheet">
<style>
  :root {
    --backdrop: #e9e9eb;
    --paper: #ffffff;
    --brand-purple: #4f2b91;
    --accent-grey: #8a8a8c;
    --body-text: #5b5b5f;
    --footer-text: #ffffff;
    --signature-tone: #efeff1;
  }
  * { box-sizing: border-box; margin: 0; padding: 0; }
  html, body {
    width: 1200px; height: 795px; overflow: hidden;
    background: var(--backdrop);
    font-family: "Open Sans", Arial, sans-serif;
  }
  .letterhead {
    position: absolute; left: 330px; top: 15px;
    width: 540px; height: 764px;
    background: var(--paper);
    box-shadow: 0 2px 10px rgba(0,0,0,0.12);
    overflow: hidden;
  }
  .brand {
    position: absolute; left: 44px; top: 78px;
    display: flex; align-items: center; gap: 7px;
    color: var(--brand-purple); font-weight: 700; font-size: 16px; letter-spacing: 0.2px;
  }
  .brand-mark { width: 10px; height: 10px; background: var(--brand-purple); }
  .letter {
    position: absolute; left: 44px; top: 150px; width: 430px;
    color: var(--body-text); font-size: 9.5px; line-height: 1.45;
  }
  .letter-date { margin-bottom: 14px; }
  .recipient { margin-bottom: 14px; }
  .salutation { font-weight: 700; margin-bottom: 12px; }
  .letter p.body { margin-bottom: 12px; }
  .signature {
    position: absolute; right: 46px; top: 498px;
    width: 88px; height: 30px;
    background: var(--signature-tone); border-radius: 3px;
  }
  .footer-wave { position: absolute; left: 0; bottom: 0; width: 540px; height: 290px; }
  .contact-address {
    position: absolute; left: 250px; bottom: 22px;
    color: var(--footer-text); font-size: 8.5px; line-height: 1.5; text-align: right;
  }
  .contact-list {
    position: absolute; right: 26px; bottom: 22px;
    list-style: none; color: var(--footer-text); font-size: 8.5px; line-height: 1.75;
  }
  .contact-list li { display: flex; align-items: center; gap: 6px; }
  .contact-icon {
    width: 9px; height: 9px; border-radius: 50%;
    background: #c9c9cc; flex: none;
  }
</style>
</head>
<body>
  <main class="letterhead">
    <div class="brand"><span class="brand-mark"></span><span class="brand-name">Halvard Realty Group, LLC</span></div>

    <section class="letter">
      <p class="letter-date">January 12, 2014</p>
      <p class="recipient">Mr. John Doe<br>President<br>AA Corporation<br>111 Street Name, Suite#<br>City, State, 12345</p>
      <p class="salutation">Dear Mr. John,</p>
      <p class="body">Lorem Ipsum is simply dummy text of the printing and typesetting industry. Lorem Ipsum has been the industry's standard dummy text ever since the 1500s, when an unknown printer took a galley of type and scrambled it to make a type specimen book. It has survived not only five centuries, but also the leap into electronic typesetting, remaining essentially unchanged.</p>
      <p class="body">The standard chunk of Lorem Ipsum used since the 1500s is reproduced below for those interested. Sections 1.10.32 and 1.10.33 from "de Finibus Bonorum et Malorum" by Cicero are also reproduced in their exact original form, accompanied by English versions from the 1914 translation by H. Rackham.</p>
      <p class="body">Lorem Ipsum is simply dummy text of the printing and typesetting industry. Lorem Ipsum has been the industry's standard dummy text ever since the 1500s, when an unknown printer took a galley of type and scrambled it to make a type specimen book. It has survived not only five centuries, but also the leap into electronic typesetting, remaining essentially unchanged. It was popularised in the</p>
    </section>

    <div class="signature" role="img" aria-label="Handwritten signature of the sender"></div>

    <svg class="footer-wave" viewBox="0 0 540 290" aria-hidden="true">
      <path d="M0,290 L0,272 C210,262 390,215 540,30 L540,290 Z" fill="var(--brand-purple)"/>
      <path d="M0,262 C210,252 385,205 535,22" fill="none" stroke="var(--accent-grey)" stroke-width="4" stroke-dasharray="110 8"/>
    </svg>

    <p class="contact-address">Suite 102 Street name, State,<br>Zip 2034, Country</p>
    <ul class="contact-list">
      <li><span class="contact-icon"></span>(00) 01234 567 890</li>
      <li><span class="contact-icon"></span>(00) 01234 567 891</li>
      <li><span class="contact-icon"></span>info@halvardrealty.com</li>
      <li><span class="contact-icon"></span>www.halvardrealty.com</li>
    </ul>
  </main>
</body>
</html>
```